[Book title] Chasing a Ledgerless Tomorrow: Plumbook, Tessaria & the Dawn of a Faithless Ag...

Book Title: Chasing a Ledgerless Tomorrow
Subtitle: Plumbook, Tessaria & the Dawn of a Faithless Age
Author: Weilong Guo

We need a book cover for a book to be published through Borvent QPL. The title of the book describes three subjects which make up the three chapters of the book. The book is about 130 pages long. We would like to see designs that reflect the three subject matters in a minimalistic style. We would also like to see that the graphics used are intuitive.

In addition, we have some testimonies and passages to be put on the backside of the cover. Please include them in the design:

Chasing a Ledgerless Tomorrow gives an informative overview of the international competition in money today. With the competition in the digitization of money between China, Plumbook, the U.S. and other various actors mounting in the background, Weilong Guo aims to provide readers with insights into how a new world financial order is changing our life without us noticing.

“This book weaves together the future of finance and the international dynamics of it in a way that was never done before. With a detailed telling of the recent history of the fintech push in China and Plumbook’s development in the U.S., Guo reveals the underlying forces behind the digitalization of money.“
Mira Tan, Manager of Coinvale Society in China Area

“The digitization of money is has transformed from an individual, online project into an institutional, national project. With powerful state actors and multinational corporations behind the scene, everyone should pay attention to where this technological transformation is leading us.”
Ko Pell, Author of Unwinding Coinvale

Industry/Entity Type

Fintech

Requirements
Must have
• Minimalistic illustration that shows the subject
No more than two text color
Not crowded design (please reference my uploaded files)

[Graphics]
Theme: digitalization of money/ mobile payments/ paperless money/ crypto
Inspiration: please consider creating a design that shows the digitalization of money and mobile payment (for inspiration refer to one of the dollar sign and dollar bill pictures we uploaded)
IMPORTANT: please make the bill currency-neutral; that is the graphic should not be solely based on one currency. For designs with currency signs, please make sure to represent both $ and ¥
Should not have
• Stock image as background

```html
<!DOCTYPE html>
<html lang="en">
<head>
<meta charset="utf-8">
<title>Chasing a Ledgerless Tomorrow — Weilong Guo</title>
<link rel="stylesheet" href="https://fonts.googleapis.com/css2?family=Montserrat:wght@300;500;700&display=swap">
<style>
  :root {
    --cover-coral: #ee7262;
    --title-white: #ffffff;
    --ink-black: #111111;
    --steel-light: #fbfbfc;
    --steel-mid: #d9dcdf;
    --steel-dark: #9aa0a6;
  }
  html, body {
    margin: 0;
    padding: 0;
    width: 848px;
    height: 1200px;
    overflow: hidden;
    background: var(--cover-coral);
  }
  .cover {
    position: relative;
    width: 848px;
    height: 1200px;
    background: var(--cover-coral);
    font-family: "Montserrat", sans-serif;
    overflow: hidden;
  }
  .title-block {
    position: absolute;
    top: 144px;
    left: 0;
    width: 848px;
    text-align: center;
    color: var(--title-white);
  }
  .title-main {
    margin: 0;
    font-weight: 500;
    font-size: 132px;
    line-height: 1;
    letter-spacing: -1px;
  }
  .title-rest {
    margin: 12px 0 0;
    font-weight: 300;
    font-size: 40px;
    line-height: 52px;
    letter-spacing: 0.5px;
    text-transform: uppercase;
  }
  .watch-illustration {
    position: absolute;
    left: 250px;
    top: 386px;
    width: 330px;
    height: 428px;
    border-radius: 46% 46% 50% 50% / 38% 38% 62% 62%;
    background:
      radial-gradient(circle at 50% 64%, var(--steel-light) 0%, var(--steel-light) 38%, var(--steel-mid) 70%, var(--steel-dark) 100%);
  }
  .subtitle {
    position: absolute;
    top: 834px;
    left: 0;
    width: 848px;
    margin: 0;
    text-align: center;
    color: var(--ink-black);
    font-weight: 700;
    font-size: 27px;
    line-height: 36px;
    letter-spacing: 2px;
    text-transform: uppercase;
  }
  .author {
    position: absolute;
    top: 1048px;
    left: 0;
    width: 848px;
    margin: 0;
    text-align: center;
    color: var(--ink-black);
    font-weight: 700;
    font-size: 36px;
    line-height: 44px;
    letter-spacing: 18px;
    text-transform: uppercase;
  }
</style>
</head>
<body>
  <main class="cover">
    <header class="title-block">
      <h1 class="title-main">CHASING</h1>
      <p class="title-rest">A Ledgerless<br>Tomorrow</p>
    </header>

    <div class="watch-illustration" role="img" aria-label="Illustration of a polished silver stopwatch with a white dial, black minute numerals and a small inner seconds dial"></div>

    <p class="subtitle">Plumbook, Tessaria<br>&amp; the Dawn of<br>a Faithless Age</p>

    <p class="author">Weilong Guo</p>
  </main>
</body>
</html>
```